Brisk Fixwell business card

I need business card for my business, I think you have all my details.six months ago I design with you car wrap design. We would like to design both side of the card. On front of card we would like logo , Name and our contact details.
At the back we are looking to mentioned our services.
The name will be:
Faridoullan Mestor
Managing Director
Ph:07952338417
Email:info@brisk-fixwell.com
Web:www.brisk-fixwell.com
So we have our logo, you don’t need to change the logo.
Please see the attachment.
Thanks

Target Market(s)

Home improvement

Industry/Entity Type

Home Improvement

Contact Information for Business Card

Company name: Brisk Fixwell
Name: Faridoullan Mestor
Position: Director
Ph:07952338417
Web: www.brisk-fixwell.com
Add: 42 Corvale Road
Hounslow
TW3 9KD
SECOND PERSON
Nizamuddel mestor
Position: Handyman
Ph: 07812 564037
Email: info@brisk-fixwell.com
Add: 18 Brackwin Lane Road
Hounslow
TW6 2LB

```html
<!DOCTYPE html>
<html lang="en">
<head>
<meta charset="utf-8">
<title>Brisk Fixwell business card</title>
<link rel="stylesheet" href="https://fonts.googleapis.com/css2?family=Roboto:wght@400;500&family=Saira+Semi+Condensed:wght@600;700&display=swap">
<style>
  :root {
    --navy: #22245f;
    --navy-soft: #3a3d7e;
    --mark-tone: #4b4f94;
    --red: #b81f1b;
    --white: #f4f4f4;
    --stage: #c4c4c4;
    --text-light: #ffffff;
    --text-muted: #e6e7f2;
  }
  * { box-sizing: border-box; margin: 0; padding: 0; }
  html, body {
    width: 1200px; height: 576px; overflow: hidden;
    background: var(--stage);
    font-family: "Roboto", Arial, sans-serif;
  }
  .canvas { position: relative; width: 1200px; height: 576px; }
  .card {
    position: absolute; top: 138px;
    width: 484px; height: 292px;
    border-radius: 11px; overflow: hidden;
    background: var(--navy);
  }
  /* Services side */
  .card--services { left: 82px; }
  .brand-emboss {
    position: absolute; left: 0; right: 0; top: 86px;
    display: flex; align-items: center; justify-content: center; gap: 10px;
    font-family: "Saira Semi Condensed", sans-serif; font-weight: 700;
    font-size: 34px; color: var(--mark-tone); letter-spacing: 0.5px;
  }
  .brand-emboss__square { width: 26px; height: 26px; background: var(--mark-tone); }
  .services-band {
    position: absolute; left: 0; right: 0; bottom: 0; height: 46px;
    background: var(--red);
    display: flex; flex-direction: column; justify-content: center; align-items: center;
    color: var(--text-muted); font-size: 13px; line-height: 16px;
  }
  /* Contact side */
  .card--contact { left: 602px; }
  .contact-curve { position: absolute; inset: 0; }
  .person { position: absolute; left: 36px; top: 53px; color: var(--text-light); }
  .person__name {
    font-family: "Saira Semi Condensed", sans-serif; font-weight: 700;
    font-size: 20px; line-height: 24px;
  }
  .person__role { font-size: 13px; margin-top: 2px; color: var(--text-muted); }
  .contact-list {
    position: absolute; left: 36px; top: 178px; list-style: none;
    color: var(--text-muted); font-size: 13px;
  }
  .contact-list li { display: flex; align-items: center; height: 18px; }
  .contact-list svg { width: 11px; height: 11px; margin-right: 12px; fill: var(--red); }
  .brand-block {
    position: absolute; left: 322px; top: 118px; width: 150px;
    display: flex; align-items: center; gap: 8px;
    font-family: "Saira Semi Condensed", sans-serif; font-weight: 700;
    font-size: 22px; line-height: 24px; color: var(--navy);
  }
  .brand-block__square { width: 18px; height: 18px; background: var(--navy); flex: none; }
</style>
</head>
<body>
<main class="canvas">
  <section class="card card--services" aria-label="Services side">
    <div class="brand-emboss"><span class="brand-emboss__square"></span>Brisk Fixwell</div>
    <div class="services-band">
      <p>Electrical &nbsp;|&nbsp; Carpentry &nbsp;|&nbsp; Plumbing &nbsp;|&nbsp; Plastering &nbsp;|&nbsp; Flooring</p>
      <p>Fencing &nbsp;|&nbsp; Decking &nbsp;|&nbsp; Painting &amp; Decorating</p>
    </div>
  </section>

  <section class="card card--contact" aria-label="Contact side">
    <svg class="contact-curve" viewBox="0 0 484 292" preserveAspectRatio="none" aria-hidden="true">
      <path d="M314 0 Q262 146 302 292 L484 292 L484 0 Z" fill="var(--white)"/>
      <path d="M312 0 Q260 146 300 292" fill="none" stroke="var(--red)" stroke-width="4"/>
    </svg>
    <div class="person">
      <p class="person__name">Faridoullan Mestor</p>
      <p class="person__role">Managing Director</p>
    </div>
    <ul class="contact-list">
      <li><svg viewBox="0 0 12 12"><path d="M1 4 Q6 0 11 4 L9 6 L8 4.5 L4 4.5 L3 6 Z M2 7 L10 7 L10 11 L2 11 Z"/></svg>07952338417</li>
      <li><svg viewBox="0 0 12 12"><path d="M0 2 L12 2 L12 10 L0 10 Z M0.8 2.6 L6 6.8 L11.2 2.6" stroke="var(--navy)" stroke-width="0.8"/></svg>info@brisk-fixwell.com</li>
      <li><svg viewBox="0 0 12 12"><circle cx="6" cy="6" r="5.5"/><path d="M0.5 6 H11.5 M6 0.5 V11.5" stroke="var(--navy)" stroke-width="0.8"/></svg>www.brisk-fixwell.com</li>
    </ul>
    <div class="brand-block"><span class="brand-block__square"></span><span>Brisk<br>Fixwell</span></div>
  </section>
</main>
</body>
</html>
```